Redesign of the current website

We would like a new format and redesign of the www.getvantoru.com website. We are a medical tech company and want our site to reflect current technology trends. VANTORU provides innovative solutions to streamline business operations of Imaging Providers and Physicians while delivering life-changing solutions to patients. Free to patients and physicians.

Target Market(s)

Imaging Providers (with a secondary appeal for physicians and patients)

Industry/Entity Type

MedTech

Coding

Coded - Design and coding required

Number of Pages Required

1 page

Font styles to use
Sans Serif

Requirements
Must have
• New clear slogan to represent who and what we do.
Nice to have
• VANTORU provides innovative solutions to streamline business operations of Imaging Providers and Physicians while delivering life-changing solutions to patients.
Should not have
• Bright Scanning or Join the revolution

```html
<!DOCTYPE html>
<html lang="en">
<head>
<meta charset="utf-8">
<title>VANTORU – Cloud-Based Imaging Platform</title>
<link rel="stylesheet" href="https://fonts.googleapis.com/css2?family=Montserrat:wght@600;700;800&family=Roboto:wght@400;500;700&display=swap">
<style>
:root{
  --green:#8cc63f;
  --green-dark:#6fae2a;
  --blue:#0e9be3;
  --blue-deep:#0b7fcf;
  --navy:#0b2a4a;
  --ink:#1e1e1e;
  --body:#7b7b7b;
  --light:#f4f4f4;
  --footer:#1c1c1c;
  --white:#fff;
}
*{margin:0;padding:0;box-sizing:border-box}
html,body{width:1200px;height:4203px;overflow:hidden}
body{position:relative;font-family:'Roboto',sans-serif;color:var(--ink);background:var(--white)}
.abs{position:absolute}
h1,h2,h3,.heading{font-family:'Montserrat',sans-serif}
.btn{position:absolute;display:flex;align-items:center;justify-content:center;border-radius:24px;background:var(--green);color:#fff;font:700 13px 'Montserrat',sans-serif;letter-spacing:.2px}
.eyebrow{font:700 17px 'Montserrat',sans-serif;color:var(--green)}
.title{font:700 31px 'Montserrat',sans-serif;color:var(--blue)}
.para{font-size:13.5px;line-height:26px;color:var(--body);text-align:justify}

/* header */
.site-header{left:0;top:0;width:1200px;height:110px;background:#fff;border-top:4px solid var(--green)}
.brand{position:absolute;display:flex;align-items:center;gap:8px;font:800 26px 'Montserrat',sans-serif;color:var(--green);white-space:nowrap}
.brand-dot{width:13px;height:13px;border-radius:50%;background:var(--blue)}
.brand-url{position:absolute;left:140px;top:84px;font:700 6px 'Roboto',sans-serif;letter-spacing:2px;color:var(--blue)}
.nav{position:absolute;left:310px;top:46px;display:flex;gap:22px;font:500 14px 'Roboto',sans-serif}
.nav .active{color:var(--green)}
.head-btn{position:absolute;top:32px;height:46px;width:120px;border-radius:23px;color:#fff;font:700 14px 'Roboto',sans-serif;display:flex;align-items:center;justify-content:center}

/* hero */
.hero{left:0;top:110px;width:1200px;height:610px;overflow:hidden;background:linear-gradient(100deg,#0a1e33 0%,#0d3a5e 45%,#1687c4 70%,#0c3556 100%)}
.hero-photo{position:absolute;inset:0;background:radial-gradient(circle at 68% 38%,rgba(40,200,255,.55),rgba(20,120,190,.2) 30%,transparent 55%)}
.hero-welcome{left:111px;top:170px;font:700 21px 'Montserrat',sans-serif;color:#fff}
.hero-title{left:108px;top:196px;display:flex;align-items:center;gap:14px}
.hero-name{font:800 62px/80px 'Montserrat',sans-serif;color:#fff;letter-spacing:1px}
.hero-rule{width:90px;height:3px;background:var(--blue);margin-top:6px}
.hero-sub{left:111px;top:281px;width:470px;font:500 16px/26px 'Roboto',sans-serif;color:#fff}
.social-ring{position:absolute;left:42px;width:34px;height:34px;border-radius:50%;border:1px solid #fff}
.social-dot{position:absolute;left:53px;width:12px;height:12px;border-radius:50%;background:#fff}
.scroll-line{left:59px;top:355px;width:1px;height:74px;background:#fff}
.scroll-text{left:30px;top:490px;transform:rotate(-90deg);font:500 9px 'Roboto',sans-serif;color:#fff;letter-spacing:.5px}
.slide-dot{position:absolute;top:494px;width:6px;height:6px;border-radius:50%;background:#fff}

/* about */
.about-photo{left:111px;top:820px;width:429px;height:411px;border-radius:12px;background:linear-gradient(135deg,#a8a29a,#d9cfc4 50%,#6d6a65)}
.about-block{left:77px;top:1097px;width:168px;height:167px;background:var(--green)}
.dot-grid{left:455px;top:784px}

/* solution */
.solution-band{left:0;top:1360px;width:1200px;height:329px;background:linear-gradient(90deg,#0e9be3,#12a4ea 60%,#0b8fd8)}
.sol-head{left:111px;top:1407px;color:#fff}
.sol-divider{left:560px;top:1405px;width:2px;height:103px;background:rgba(255,255,255,.7)}
.sol-text{left:612px;top:1415px;width:476px;font-size:13.5px;line-height:26px;color:#fff;text-align:justify}
.card{position:absolute;top:1555px;width:308px;height:475px;background:#fff;border-radius:10px;box-shadow:0 4px 18px rgba(0,0,0,.12)}
.card-photo{position:absolute;left:6px;top:6px;right:6px;height:208px;border-radius:8px}
.card h3{position:absolute;left:22px;top:232px;font:700 17px 'Montserrat',sans-serif;color:var(--blue)}
.card ul{position:absolute;left:22px;top:266px;width:262px;list-style:none}
.card li{position:relative;padding-left:27px;font-size:12.5px;line-height:22px;color:var(--body);margin-bottom:6px}
.card li::before{content:"";position:absolute;left:0;top:5px;width:12px;height:12px;border-radius:50%;background:var(--green)}
.card li::after{content:"";position:absolute;left:3px;top:9px;width:4px;height:4px;border-top:1.5px solid #fff;border-right:1.5px solid #fff;transform:rotate(45deg)}
.card .btn{left:22px;top:406px;width:122px;height:46px}

/* empower */
.empower{left:0;top:2131px;width:600px;height:445px;background:var(--light)}
.empower-photo{left:600px;top:2131px;width:600px;height:445px;background:linear-gradient(120deg,#2e3f4f,#8a97a3 50%,#d5dbe0)}

/* why choose */
.why{left:0;top:2576px;width:1200px;height:747px;background:linear-gradient(180deg,#7fbe36,#8cc63f 50%,#7cb934)}
.why-eyebrow{left:0;width:1200px;top:2632px;text-align:center;font:700 17px 'Montserrat',sans-serif;color:#fff}
.why-title{left:0;width:1200px;top:2658px;text-align:center;font:700 29px 'Montserrat',sans-serif;color:#fff}
.pill{position:absolute;width:474px;height:118px;border-radius:59px;background:#fff;box-shadow:0 4px 14px rgba(0,0,0,.12)}
.pill p{position:absolute;top:50%;transform:translateY(-50%);font-size:13.5px;line-height:25px;color:var(--body)}
.pill.left p{left:42px;width:315px;text-align:right}
.pill.right p{left:130px;width:310px;text-align:left}
.pill .icon{position:absolute;top:8px;width:102px;height:102px;border-radius:50%;display:flex;align-items:center;justify-content:center;border:4px solid #fff;box-shadow:0 0 0 2px rgba(0,0,0,.05)}
.pill.left .icon{right:8px;background:var(--blue)}
.pill.right .icon{left:8px;background:var(--green)}

/* testimonials */
.test-eyebrow{left:0;width:1200px;top:3397px;text-align:center;font:700 17px 'Montserrat',sans-serif;color:var(--green)}
.test-title{left:0;width:1200px;top:3423px;text-align:center;font:700 34px 'Montserrat',sans-serif;color:var(--blue)}
.review{position:absolute;top:3491px;width:309px;height:231px;background:#fff;box-shadow:0 3px 16px rgba(0,0,0,.1)}
.avatar{position:absolute;left:25px;top:34px;width:62px;height:62px;border-radius:50%;background:linear-gradient(135deg,#c9c2ba,#6f7a86)}
.review h4{position:absolute;left:108px;top:46px;font:700 19px 'Montserrat',sans-serif}
.review .meta{position:absolute;left:108px;top:74px;font-size:9px;color:#aaa;display:flex;gap:8px;align-items:center}
.stars{color:#f4b400;font-size:9px;letter-spacing:1px}
.review p{position:absolute;left:25px;top:124px;width:260px;font-size:12.5px;line-height:22px;color:var(--body);text-align:justify}

/* footer */
.footer{left:0;top:3815px;width:1200px;height:335px;background:var(--footer)}
.foot-col h5{position:absolute;font:700 16px 'Roboto',sans-serif;color:#fff}
.foot-col h5::after{content:"";position:absolute;left:0;top:28px;width:34px;height:2px;background:var(--blue)}
.foot-list{position:absolute;list-style:none}
.foot-list li{position:relative;padding-left:34px;height:33px;font-size:14.5px;color:#fff}
.foot-list li::before{content:"";position:absolute;left:0;top:3px;width:12px;height:12px;border-radius:50%;background:var(--green)}
.contact-list li::before{border-radius:2px;width:10px;height:10px;top:4px}
.foot-social{position:absolute;top:4077px;width:38px;height:38px;border-radius:50%;border:1px solid #fff}
.bottom-bar{left:0;top:4150px;width:1200px;height:53px;background:var(--blue);color:#fff;font-size:11.5px;display:flex;align-items:center;justify-content:center}
</style>
</head>
<body>

<!-- Header -->
<header class="site-header abs">
  <div class="brand" style="left:111px;top:34px"><span>VANTORU</span><span class="brand-dot"></span></div>
  <div class="brand-url">WWW.GETVANTORU.COM</div>
  <nav class="nav"><span class="active">HOME</span><span>ABOUT US</span><span>STORAGE</span><span>SOLUTION</span><span>NEWS</span><span>CONTACT</span></nav>
  <div class="head-btn" style="left:841px;background:var(--blue)">REGISTER</div>
  <div class="head-btn" style="left:968px;background:var(--green)">LOGIN</div>
</header>

<!-- Hero -->
<section class="hero abs">
  <div class="hero-photo" role="img" aria-label="Hand holding a tablet with a glowing digital medical network globe"></div>
  <div class="hero-welcome abs">WELCOME TO</div>
  <div class="hero-title abs"><h1 class="hero-name">VANTORU</h1><span class="hero-rule"></span></div>
  <p class="hero-sub abs">"Imaging, shared in an instant." Diagnostic images &amp; reports for providers, physicians and patients</p>
  <div class="btn" style="left:111px;top:356px;width:129px;height:46px">GET STARTED</div>
  <span class="social-ring" style="top:219px"></span>
  <span class="social-dot" style="top:269px"></span>
  <span class="social-dot" style="top:308px"></span>
  <div class="scroll-line abs"></div>
  <div class="scroll-text abs">SCROLL DOWN</div>
  <span class="slide-dot" style="left:563px"></span>
  <span class="slide-dot" style="left:583px;width:14px;height:14px;top:490px;border:1px solid #fff;background:none"></span>
  <span class="slide-dot" style="left:610px"></span>
  <span class="slide-dot" style="left:633px"></span>
  <svg class="abs" style="left:0;top:520px" width="1200" height="92" viewBox="0 0 1200 92">
    <path d="M0 92 L0 70 C60 70 80 60 130 62 C200 66 230 48 300 52 C380 56 420 40 470 42 C520 6 600 -6 660 30 C700 2 780 4 800 40 C840 52 880 58 940 60 C1000 38 1060 36 1100 52 C1140 40 1180 42 1200 48 L1200 92 Z" fill="#fff"/>
  </svg>
  <svg class="abs" style="left:48px;top:568px" width="24" height="34" viewBox="0 0 24 34"><circle cx="12" cy="10" r="9" fill="var(--green)"/><path d="M12 12 V32 M5 25 L12 32 L19 25" stroke="var(--green-dark)" stroke-width="2" fill="none"/></svg>
</section>

<!-- About -->
<section class="about">
  <div class="about-block abs"></div>
  <div class="about-photo abs" role="img" aria-label="Carer with a smiling senior woman looking at a tablet"></div>
  <svg class="dot-grid abs" width="120" height="120">
    <defs><pattern id="dots" width="12" height="12" patternUnits="userSpaceOnUse"><circle cx="3" cy="3" r="1.6" fill="#c9c9c9"/></pattern></defs>
    <rect width="120" height="120" fill="url(#dots)"/>
  </svg>
  <div class="eyebrow abs" style="left:612px;top:864px">ABOUT US</div>
  <h2 class="title abs" style="left:612px;top:893px">THINKING AHEAD</h2>
  <p class="para abs" style="left:612px;top:950px;width:476px">There are so many competing pressures on healthcare providers today; meaningful use, data security, managing costs and of course increasing revenue. Solving all of these issues can sometimes seem like a mine field... what systems should I buy, how do I ensure data security while exposing it in patient or physician portals, how can I maintain or reduce my costs while meeting all of these requirements.</p>
  <div class="btn" style="left:612px;top:1135px;width:137px;height:46px">LEARN MORE</div>
</section>

<!-- Solution -->
<section class="solution">
  <div class="solution-band abs"></div>
  <div class="sol-head abs">
    <div style="font:700 17px 'Montserrat',sans-serif">OUR SOLUTION</div>
    <div style="font:700 23px/32px 'Montserrat',sans-serif;margin-top:22px">REVOLUTIONARY CENTRALIZED<br>CLOUD-BASED PLATFORM</div>
  </div>
  <div class="sol-divider abs"></div>
  <p class="sol-text abs">Enabling healthcare providers, payers, radiology imaging companies &amp; patients with secure access to real-time patient diagnostic images and reports sharing across organizational boundaries.</p>

  <article class="card" style="left:111px">
    <div class="card-photo" role="img" aria-label="Radiographer preparing a patient for a CT scan" style="background:linear-gradient(135deg,#dfe7ee,#9fb3c6 55%,#e8eef3)"></div>
    <h3>IMAGE PROVIDERS</h3>
    <ul><li>Reduce costs on producing image CDs, local storage &amp; labor</li><li>Most secure network for images &amp; report sharing</li><li>Physician receives automated progress</li></ul>
    <div class="btn">READ MORE</div>
  </article>
  <article class="card" style="left:447px">
    <div class="card-photo" role="img" aria-label="Physicians reviewing scan images on monitors" style="background:linear-gradient(135deg,#e6eaee,#7d8c99 60%,#3e4a55)"></div>
    <h3>PHYSICIANS</h3>
    <ul><li>Automated notification &amp; alerts systems</li><li>Creates flexibility in remote/Telemedicine capabilities</li><li>Web-based &amp; easy to use!</li></ul>
    <div class="btn">READ MORE</div>
  </article>
  <article class="card" style="left:781px">
    <div class="card-photo" role="img" aria-label="Patient with a coffee cup using a laptop" style="background:linear-gradient(135deg,#b6c3cf,#e4e9ee 50%,#8d99a5)"></div>
    <h3>PATIENTS</h3>
    <ul><li>Easily accessible &amp; secure medical imaging &amp; reports</li><li>Patient owns images &amp; can direct who sees them</li><li>VANTORU is Free &amp; easy to setup</li></ul>
    <div class="btn">READ MORE</div>
  </article>
</section>

<!-- Empower -->
<section>
  <div class="empower abs"></div>
  <div class="empower-photo abs" role="img" aria-label="Doctor with a stethoscope reading a tablet"></div>
  <div class="eyebrow abs" style="left:111px;top:2214px">CARING IS SHARING</div>
  <h2 class="abs" style="left:111px;top:2245px;font:700 23px/32px 'Montserrat',sans-serif;color:var(--blue)">EMPOWER PATIENTS<br>&amp; HEALTHCARE PROVIDERS</h2>
  <p class="para abs" style="left:111px;top:2329px;width:430px">VANTORU allows the ownership of the images to be in the Patient's hands and enables interoperability between Diagnostic Imaging Centers, Patients and Physicians.</p>
  <div class="btn" style="left:111px;top:2440px;width:137px;height:46px">LEARN MORE</div>
</section>

<!-- Why choose -->
<section>
  <div class="why abs" role="img" aria-label="Green backdrop with faint medical network graphics"></div>
  <div class="why-eyebrow abs">WHY CHOOSE US</div>
  <h2 class="why-title abs">PROBLEM &amp; SOLUTION</h2>

  <div class="pill left" style="left:111px;top:2728px"><p>No real-time solutions today for sharing radiology images &amp; reports between physicians, imaging providers and patients</p>
    <div class="icon"><svg width="54" height="54" fill="none" stroke="#fff" stroke-width="2.5"><circle cx="30" cy="30" r="18"/><path d="M30 30 L30 19 M30 30 L38 34 M6 26 H14 M4 34 H12"/></svg></div></div>
  <div class="pill right" style="left:613px;top:2728px"><div class="icon"><svg width="54" height="54" fill="none" stroke="#fff" stroke-width="2.5"><path d="M14 34 A9 9 0 0 1 16 17 A12 12 0 0 1 38 16 A9 9 0 0 1 40 34 Z"/><path d="M20 34 V46 M27 34 V46 M34 34 V46"/></svg></div>
    <p>No real-time solutions today for sharing radiology images &amp; reports between physicians, imaging providers and patients</p></div>

  <div class="pill left" style="left:111px;top:2865px"><p>Too much duplication of imaging</p>
    <div class="icon"><svg width="54" height="54" fill="none" stroke="#fff" stroke-width="2.5"><rect x="18" y="10" width="24" height="32" rx="3"/><path d="M12 16 V46 H34"/></svg></div></div>
  <div class="pill right" style="left:613px;top:2865px"><div class="icon"><svg width="54" height="54" fill="none" stroke="#fff" stroke-width="2.5"><rect x="10" y="10" width="34" height="34" rx="3"/><path d="M10 21 H44 M10 32 H44 M16 16 H24 M16 27 H24 M16 38 H24"/></svg></div>
    <p>Eliminated localized storage costs</p></div>

  <div class="pill left" style="left:111px;top:3001px"><p>No notification to the patient following physician review of image and report</p>
    <div class="icon"><svg width="54" height="54" fill="none" stroke="#fff" stroke-width="2.5"><circle cx="22" cy="22" r="7"/><path d="M10 46 C10 34 34 34 34 46"/><rect x="30" y="8" width="16" height="14" rx="2"/><path d="M38 11 V19 M34 15 H42"/></svg></div></div>
  <div class="pill right" style="left:613px;top:3001px"><div class="icon"><svg width="54" height="54" fill="none" stroke="#fff" stroke-width="2.5"><circle cx="27" cy="14" r="7"/><path d="M27 10 V18 M23 14 H31"/><circle cx="15" cy="33" r="4"/><circle cx="27" cy="33" r="4"/><circle cx="39" cy="33" r="4"/><path d="M8 46 C8 40 22 40 22 46 M20 46 C20 40 34 40 34 46 M32 46 C32 40 46 40 46 46"/></svg></div>
    <p>Patient owns the image and report &amp; optionally assigns rights to providers</p></div>

  <div class="pill left" style="left:111px;top:3138px"><p>Too many manual processes today in order for providers to access patient images &amp; reports</p>
    <div class="icon"><svg width="54" height="54" fill="none" stroke="#fff" stroke-width="2.5"><rect x="8" y="12" width="36" height="26" rx="3"/><path d="M8 20 H44 M14 30 H26"/><circle cx="40" cy="38" r="8"/><path d="M36 38 L39 41 L44 35"/></svg></div></div>
  <div class="pill right" style="left:613px;top:3138px"><div class="icon"><svg width="54" height="54" fill="none" stroke="#fff" stroke-width="2.5"><rect x="18" y="22" width="18" height="16" rx="2"/><path d="M21 22 V17 A6 6 0 0 1 33 17 V22 M10 12 H16 M38 12 H44 M10 44 H16 M38 44 H44 M12 12 V20 M42 12 V20"/></svg></div>
    <p>Provides secure audit trail</p></div>
</section>

<!-- Testimonials -->
<section>
  <div class="test-eyebrow abs">TESTIMONIALS</div>
  <h2 class="test-title abs">PATIENT REVIEWS</h2>
  <svg class="abs" style="left:48px;top:3596px" width="26" height="20"><path d="M24 10 H3 M10 3 L3 10 L10 17" stroke="#bbb" stroke-width="1.8" fill="none"/></svg>
  <svg class="abs" style="left:1127px;top:3596px" width="26" height="20"><path d="M2 10 H23 M16 3 L23 10 L16 17" stroke="#555" stroke-width="1.8" fill="none"/></svg>

  <article class="review" style="left:111px">
    <div class="avatar" role="img" aria-label="Reviewer portrait"></div>
    <h4>Elena Marsh</h4><div class="meta"><span class="stars">★★★★★</span><span>March 2022</span></div>
    <p>I was so happy that I no longer have to manage my image &amp; report. Standing in line and waiting for them to cut my CD was intolerable. VANTORU makes it easy!</p>
  </article>
  <article class="review" style="left:446px">
    <div class="avatar" role="img" aria-label="Reviewer portrait"></div>
    <h4>Tobias Reed</h4><div class="meta"><span class="stars">★★★★★</span><span>March 2022</span></div>
    <p>VANTORU offers superior real-time online delivery service that helped my Doctor work effectively. VANTORU is easily available to providers no matter where I'm located.</p>
  </article>
  <article class="review" style="left:780px">
    <div class="avatar" role="img" aria-label="Reviewer portrait"></div>
    <h4>Marcus Hale</h4><div class="meta"><span class="stars">★★★★★</span><span>March 2022</span></div>
    <p>I had an X-Ray taken by my Dr and was so thrilled that I did not have to pay for another image when they referred me to another provider</p>
  </article>
</section>

<!-- Footer -->
<footer>
  <svg class="abs" style="left:0;top:3780px" width="1200" height="40" viewBox="0 0 1200 40">
    <path d="M0 40 V22 C60 10 120 8 180 20 C260 30 320 26 380 22 C460 16 520 24 600 28 C680 30 740 14 800 8 C860 4 900 20 960 22 C1040 24 1100 6 1160 2 C1180 2 1200 6 1200 6 V40 Z" fill="var(--footer)"/>
  </svg>
  <div class="footer abs"></div>
  <div class="brand" style="left:111px;top:3982px;font-size:40px"><span>VANTORU</span><span class="brand-dot" style="width:15px;height:15px"></span></div>
  <div class="abs" style="left:165px;top:4040px;font:700 8px 'Roboto',sans-serif;letter-spacing:3px;color:var(--blue)">WWW.GETVANTORU.COM</div>
  <span class="foot-social" style="left:154px;background:var(--green);border-color:var(--green)"></span>
  <span class="foot-social" style="left:198px"></span>
  <span class="foot-social" style="left:243px"></span>

  <div class="foot-col"><h5 style="left:417px;top:3932px">NAVIGATION</h5></div>
  <ul class="foot-list" style="left:419px;top:3981px"><li>Home</li><li>About Us</li><li>Storage</li><li>Solution</li><li>Contact</li></ul>

  <div class="foot-col"><h5 style="left:627px;top:3932px">QUICK LINKS</h5></div>
  <ul class="foot-list" style="left:629px;top:3981px"><li>News</li><li>PrivacyPolicy</li><li>Terms Of Use</li></ul>

  <div class="foot-col"><h5 style="left:885px;top:3932px">CONTACT</h5></div>
  <ul class="foot-list contact-list" style="left:887px;top:3981px">
    <li style="height:55px;line-height:22px">412 W. Linden Ave.,<br>Carver, Ohio 45021</li>
    <li>1-833-555-0142</li><li>info@getvantoru.com</li>
  </ul>
  <svg class="abs" style="left:1064px;top:4128px" width="26" height="34"><circle cx="13" cy="22" r="11" fill="var(--green)"/><path d="M13 24 V2 M7 8 L13 2 L19 8" stroke="#fff" stroke-width="2" fill="none"/></svg>
  <div class="bottom-bar abs">© 2022&nbsp;<b>VANTORU</b>&nbsp;·&nbsp; All Rights Reserved</div>
</footer>

</body>
</html>
```